Redesign of business card for Cedar Ridge Mechanical

We are looking for a new design for our business cards for Cedar Ridge Mechanical. We are a plumbing & HVAC construction company, operating on the West Coast of Canada and USA. Logo attached.
Industry/Entity Type
Construction - Plumbing & HVAC
Contact Information for Business Card
Name, address, phone numbers, email, website address
Look and feel
Each slider illustrates characteristics of the customer's brand and the style your logo design should communicate.

```html
<!DOCTYPE html>
<html lang="en">
<head>
<meta charset="utf-8">
<title>Cedar Ridge Mechanical – Business Card</title>
<link rel="stylesheet" href="https://fonts.googleapis.com/css2?family=Montserrat:wght@400;500;700;800&display=swap">
<style>
  :root {
    --backdrop: #e9e9eb;
    --ink: #111111;
    --card-black: #141414;
    --gloss: #3a3a3a;
    --paper: #ffffff;
    --grey: #9a9a9a;
    --text: #1a1a1a;
  }
  * { margin: 0; padding: 0; box-sizing: border-box; }
  html, body { width: 1200px; height: 913px; overflow: hidden; }
  body {
    background: var(--backdrop);
    font-family: "Montserrat", sans-serif;
    position: relative;
  }
  .card {
    position: absolute;
    width: 560px;
    height: 320px;
    border-radius: 18px;
    overflow: hidden;
    box-shadow: 0 10px 30px rgba(0,0,0,0.18);
  }
  .card-back {
    left: 90px; top: 90px;
    background: var(--card-black);
    display: flex; align-items: center; justify-content: center; gap: 18px;
  }
  .card-back .mark-square {
    width: 46px; height: 46px; border: 6px solid var(--gloss);
  }
  .card-back .brand-name {
    color: var(--gloss);
    font-weight: 800;
    font-size: 30px;
    letter-spacing: 1px;
    line-height: 1.1;
    text-transform: uppercase;
  }
  .card-front {
    left: 550px; top: 500px;
    background: var(--paper);
  }
  .front-wave { position: absolute; inset: 0; }
  .front-brand {
    position: absolute; left: 34px; top: 36px;
    display: flex; align-items: center; gap: 12px;
  }
  .front-brand .mark-square {
    width: 34px; height: 34px; border: 5px solid var(--ink);
  }
  .front-brand .brand-name {
    font-weight: 800; font-size: 17px; color: var(--ink);
    text-transform: uppercase; line-height: 1.15; letter-spacing: 0.5px;
  }
  .address {
    position: absolute; left: 34px; top: 130px;
    font-size: 15px; color: var(--text); line-height: 1.35;
  }
  .contact-list {
    position: absolute; left: 34px; top: 190px;
    list-style: none; font-size: 15px; color: var(--text);
  }
  .contact-list li { display: flex; align-items: center; gap: 10px; line-height: 1.55; }
  .contact-list svg { width: 13px; height: 13px; fill: var(--ink); }
  .person {
    position: absolute; right: 36px; top: 20px; text-align: right;
  }
  .person .name { font-weight: 800; font-size: 18px; color: var(--ink); }
  .person .role { font-size: 13px; color: var(--text); margin-top: 2px; }
  .person-bar {
    position: absolute; right: 0; top: 18px; width: 18px; height: 44px; background: var(--ink);
  }
  .wave-brand {
    position: absolute; right: 26px; top: 150px;
    display: flex; align-items: center; gap: 10px;
  }
  .wave-brand .mark-square { width: 30px; height: 30px; border: 5px solid var(--paper); }
  .wave-brand .brand-name {
    color: var(--paper); font-weight: 800; font-size: 15px;
    text-transform: uppercase; line-height: 1.15;
  }
</style>
</head>
<body>
  <section class="card card-back">
    <span class="mark-square"></span>
    <span class="brand-name">Cedar Ridge<br>Mechanical</span>
  </section>

  <section class="card card-front">
    <svg class="front-wave" viewBox="0 0 560 320" preserveAspectRatio="none">
      <path d="M0 320 C150 312 300 290 380 215 C310 300 160 316 0 320 Z" fill="var(--grey)"/>
      <path d="M215 320 C330 298 380 225 420 160 C445 122 490 112 560 112 L560 320 Z" fill="var(--ink)"/>
    </svg>

    <div class="front-brand">
      <span class="mark-square"></span>
      <span class="brand-name">Cedar Ridge<br>Mechanical</span>
    </div>

    <p class="address">Your address, City<br>State, Zip 1234</p>

    <ul class="contact-list">
      <li><svg viewBox="0 0 24 24"><path d="M6.6 10.8a15.1 15.1 0 0 0 6.6 6.6l2.2-2.2a1 1 0 0 1 1-.25 11.4 11.4 0 0 0 3.6.57 1 1 0 0 1 1 1V20a1 1 0 0 1-1 1A17 17 0 0 1 3 4a1 1 0 0 1 1-1h3.5a1 1 0 0 1 1 1c0 1.25.2 2.45.57 3.57a1 1 0 0 1-.25 1z"/></svg>123 456 789</li>
      <li><svg viewBox="0 0 24 24"><path d="M2 5h20v14H2z M4 7v.5l8 5 8-5V7l-8 5z" fill-rule="evenodd"/></svg>info@yourgmail.com</li>
      <li><svg viewBox="0 0 24 24"><circle cx="12" cy="12" r="10"/></svg>www.yourwebsite.com</li>
    </ul>

    <div class="person">
      <p class="name">DANIEL HARTLEY</p>
      <p class="role">Managing Director</p>
    </div>
    <span class="person-bar"></span>

    <div class="wave-brand">
      <span class="mark-square"></span>
      <span class="brand-name">Cedar Ridge<br>Mechanical</span>
    </div>
  </section>
</body>
</html>
```